Brivo Hair

Hello - our company Vantor 4 develops novel products for the skin, & hair care industry as well as dietary supplements. We're looking for a label design for a new product. The product is a premium hair loss/growth supplement. Our primary demo is women ages 45-65. I attached the brand logo & some competitive product designs that we find attractive.

I've been traveling & have not had the time to adequately review the designs, please be patient with me.

```html
<!DOCTYPE html>
<html lang="en">
<head>
<meta charset="utf-8">
<title>Brivo Hair – Supplement Label</title>
<link rel="stylesheet" href="https://fonts.googleapis.com/css2?family=Michroma&family=Cinzel:wght@700&family=Tinos:wght@700&family=Saira:wght@400;700;800&family=Oswald:wght@500&display=swap">
<style>
  :root {
    --stage: #5b5b5b;
    --blue-deep: #0a4aa8;
    --blue-mid: #1673d6;
    --blue-bright: #2aaef5;
    --sky: #d6eef8;
    --sky-pale: #eef7fb;
    --silver-light: #f2f2f2;
    --silver-dark: #9a9a9a;
    --ink: #151a22;
    --brand-grey: #8fa3b3;
    --white: #ffffff;
    --body-ink: #1d3550;
  }
  * { margin: 0; padding: 0; box-sizing: border-box; }
  html, body { width: 692px; height: 1200px; overflow: hidden; }
  body {
    background: radial-gradient(ellipse at 60% 40%, #7a7a7a 0%, var(--stage) 55%, #444 100%);
    position: relative;
  }
  .label {
    position: absolute;
    left: 36px; top: 198px;
    width: 620px; height: 805px;
    box-shadow: 0 18px 40px rgba(0,0,0,.45);
  }
  .label-shapes { position: absolute; inset: 0; }
  .label-text { position: absolute; left: 0; width: 100%; text-align: center; }

  .company-name {
    top: 50px;
    font-family: "Michroma", sans-serif;
    font-size: 40px; letter-spacing: -1px;
    color: var(--white);
  }
  .tagline {
    top: 129px;
    font-family: "Michroma", sans-serif;
    font-size: 17px; letter-spacing: 1px;
    color: var(--white);
  }
  .extract-box {
    position: absolute;
    left: 80px; top: 229px; width: 461px; height: 46px;
    border: 2px solid var(--blue-deep); border-radius: 3px;
    font-family: "Cinzel", serif; font-weight: 700;
    font-size: 25px; letter-spacing: 3px; color: var(--ink);
    display: flex; align-items: center; justify-content: center;
  }
  .product-name {
    top: 292px;
    font-family: "Michroma", sans-serif;
    font-size: 58px; letter-spacing: 1px;
    color: var(--brand-grey);
  }
  .strength {
    top: 399px;
    font-family: "Cinzel", serif; font-weight: 700;
    font-size: 32px; letter-spacing: 7px; color: var(--ink);
  }
  .formula {
    top: 455px;
    font-family: "Tinos", serif; font-weight: 700;
    font-size: 43px; letter-spacing: 1px; color: var(--white);
  }
  .audience {
    top: 500px;
    font-family: "Tinos", serif; font-weight: 700;
    font-size: 84px; line-height: 1; color: var(--white);
  }
  .benefits {
    position: absolute; left: 215px; top: 618px; width: 380px;
    list-style: none;
    font-family: "Saira", sans-serif; font-size: 14.5px; line-height: 20px;
    color: var(--body-ink);
  }
  .benefits li { position: relative; padding-left: 27px; margin-bottom: 16px; }
  .benefits svg { position: absolute; left: 0; top: 2px; }
  .count {
    position: absolute; left: 97px; top: 700px; width: 93px; text-align: center;
    font-family: "Saira", sans-serif; font-weight: 800;
    font-size: 46px; line-height: 1; color: var(--ink);
  }
  .count-unit {
    position: absolute; left: 97px; top: 759px; width: 93px; text-align: center;
    font-family: "Oswald", sans-serif; font-weight: 500;
    font-size: 15px; letter-spacing: .5px; color: var(--white);
  }
  .category {
    position: absolute; left: 196px; right: 14px; top: 762px; text-align: center;
    font-family: "Oswald", sans-serif; font-weight: 500;
    font-size: 18px; letter-spacing: .3px; color: var(--white);
  }
</style>
</head>
<body>
  <div class="label">
    <svg class="label-shapes" viewBox="0 0 620 805" width="620" height="805">
      <defs>
        <linearGradient id="sky-fill" x1="0" y1="0" x2="1" y2="1">
          <stop offset="0" stop-color="#e9f5fa"/>
          <stop offset=".5" stop-color="#cdeaf7"/>
          <stop offset="1" stop-color="#e4f2f8"/>
        </linearGradient>
        <linearGradient id="header-fill" x1="0" y1="0" x2="1" y2="0">
          <stop offset="0" stop-color="#0c52b4"/>
          <stop offset=".55" stop-color="#2eaff7"/>
          <stop offset="1" stop-color="#0a3fa6"/>
        </linearGradient>
        <linearGradient id="band-fill" x1="0" y1="0" x2="1" y2="0">
          <stop offset="0" stop-color="#0a48a6"/>
          <stop offset=".5" stop-color="#1d8ee8"/>
          <stop offset="1" stop-color="#0a48a6"/>
        </linearGradient>
        <linearGradient id="silver-fill" x1="0" y1="0" x2="1" y2="0">
          <stop offset="0" stop-color="#a8a8a8"/>
          <stop offset=".5" stop-color="#f4f4f4"/>
          <stop offset="1" stop-color="#a8a8a8"/>
        </linearGradient>
        <linearGradient id="badge-fill" x1="0" y1="0" x2="1" y2="0">
          <stop offset="0" stop-color="#b5b5b5"/>
          <stop offset=".5" stop-color="#ffffff"/>
          <stop offset="1" stop-color="#b5b5b5"/>
        </linearGradient>
      </defs>

      <rect width="620" height="805" fill="url(#sky-fill)" role="img" aria-label="Faint pale-blue molecular hexagon pattern background"/>

      <g class="header">
        <polygon points="0,0 620,0 620,134 520,134 480,194 310,214 140,194 105,134 0,134" fill="url(#header-fill)"/>
        <rect x="0" y="132" width="105" height="5" fill="url(#silver-fill)"/>
        <rect x="520" y="132" width="100" height="5" fill="url(#silver-fill)"/>
        <polyline points="138,198 310,219 482,198" fill="none" stroke="url(#silver-fill)" stroke-width="5"/>
      </g>

      <rect class="strength-band" x="0" y="396" width="620" height="49" fill="url(#silver-fill)"/>
      <g class="formula-band">
        <rect x="0" y="445" width="620" height="88" fill="url(#band-fill)"/>
        <polygon points="0,532 620,532 537,587 88,587" fill="url(#band-fill)"/>
        <polygon points="0,532 88,587 60,587 0,548" fill="#e4f2f8"/>
        <polygon points="620,532 537,587 565,587 620,548" fill="#e4f2f8"/>
      </g>

      <g class="footer-bar">
        <rect x="0" y="754" width="620" height="51" fill="var(--blue-deep)"/>
        <rect x="0" y="752" width="620" height="3" fill="#7fb4e6"/>
      </g>

      <g class="count-badge">
        <path d="M97,805 V736 Q97,693 143.5,693 Q190,693 190,736 V805 Z" fill="url(#badge-fill)" stroke="#9a9a9a" stroke-width="1"/>
        <rect x="101" y="755" width="85" height="27" fill="var(--blue-deep)"/>
      </g>
    </svg>

    <div class="label-text company-name">VANTOR 4</div>
    <div class="label-text tagline">MEDICALLY PROVEN</div>
    <div class="extract-box">HE SHOULD 12:1 EXTRACT</div>
    <div class="label-text product-name">BRIVO HAIR</div>
    <div class="label-text strength">CLINICAL STRENGTH</div>
    <div class="label-text formula">ADVANCE FORMULA</div>
    <div class="label-text audience">WOMEN</div>

    <ul class="benefits">
      <li>
        <svg width="18" height="18" viewBox="0 0 18 18"><circle cx="9" cy="9" r="8" fill="none" stroke="#1673d6" stroke-width="1.4"/><polyline points="5,9.2 8,12 13,6.2" fill="none" stroke="#1673d6" stroke-width="1.6"/></svg>
        Lorem ipsum dolor sit amet, consectetur adipiscing elit, sed do eiusmod tempor incididunt ut labore et dolore magna aliqua.
      </li>
      <li>
        <svg width="18" height="18" viewBox="0 0 18 18"><circle cx="9" cy="9" r="8" fill="none" stroke="#1673d6" stroke-width="1.4"/><polyline points="5,9.2 8,12 13,6.2" fill="none" stroke="#1673d6" stroke-width="1.6"/></svg>
        Ut enim ad minim veniam, quis nostrud exercitation ullamco laboris nisi ut
      </li>
    </ul>

    <div class="count">60</div>
    <div class="count-unit">CAPSULES</div>
    <div class="category">PREMIUM HAIR LOSS/GROWTH SUPPLEMENT</div>
  </div>
</body>
</html>
```